Letterhead designs for Property Management firm

Would like to see some different letterhead/envelope designs We are a residential property management company. We would like to see designs that utilize blue/grays/black

```html
<!DOCTYPE html>
<html lang="en">
<head>
<meta charset="utf-8">
<title>Harborline Property Management – Stationery</title>
<link href="https://fonts.googleapis.com/css2?family=Open+Sans:wght@400;600;700&display=swap" rel="stylesheet">
<style>
  :root {
    --backdrop: #ababab;
    --paper: #ffffff;
    --ink: #1e1e1e;
    --brand-blue: #1457a8;
    --brand-black: #1a1a1a;
    --muted: #444444;
    --shadow: rgba(0,0,0,0.28);
  }
  html, body {
    margin: 0;
    width: 1200px;
    height: 1200px;
    overflow: hidden;
    background: var(--backdrop);
    font-family: "Open Sans", Arial, sans-serif;
    color: var(--ink);
  }
  .sheet {
    position: absolute;
    background: var(--paper);
    box-shadow: 0 -6px 14px var(--shadow);
    overflow: hidden;
  }
  .letterhead { left: 52px; top: 117px; width: 521px; height: 674px; }
  .envelope { left: 638px; width: 511px; height: 229px; }
  .envelope-front-band { top: 118px; }
  .envelope-back-blue { top: 372px; }
  .envelope-front-plain { top: 626px; }
  .envelope-back-plain { top: 881px; }

  .brand-mark {
    position: absolute;
    display: flex;
    align-items: center;
    gap: 7px;
    font-weight: 700;
    color: var(--brand-blue);
    line-height: 1.1;
  }
  .brand-square { background: var(--brand-blue); flex: none; }
  .letterhead .brand-mark { left: 62px; top: 40px; font-size: 16px; }
  .letterhead .brand-square { width: 16px; height: 16px; }
  .envelope .brand-mark { left: 14px; top: 18px; font-size: 9px; gap: 5px; }
  .envelope .brand-square { width: 8px; height: 8px; }

  .contact-block {
    position: absolute;
    left: 357px;
    top: 42px;
    padding-left: 7px;
    border-left: 1px solid var(--brand-blue);
    font-size: 7.4px;
    line-height: 11.5px;
  }
  .contact-row { display: flex; align-items: center; gap: 5px; }
  .contact-row svg { width: 7px; height: 7px; flex: none; }
  .contact-address { margin-top: 3px; line-height: 9px; }

  .recipient {
    position: absolute;
    left: 62px;
    top: 139px;
    font-size: 8.6px;
    font-weight: 600;
    line-height: 17.8px;
  }
  .letter-body {
    position: absolute;
    left: 62px;
    top: 228px;
    width: 410px;
    font-size: 8.6px;
    line-height: 17.8px;
    color: #2a2a2a;
  }
  .letter-body p { margin: 0 0 17.8px; }
  .sign-off { position: absolute; left: 62px; top: 495px; font-size: 8.6px; }
  .signature-area {
    position: absolute;
    left: 62px;
    top: 516px;
    width: 108px;
    height: 48px;
    background: linear-gradient(90deg, #f2f2f2, #e6e6e6);
  }
  .signer-title { position: absolute; left: 62px; top: 567px; font-size: 8.6px; }

  .envelope-address {
    position: absolute;
    left: 14px;
    top: 59px;
    font-size: 6.2px;
    line-height: 7.6px;
    color: var(--muted);
  }
  .footer-band {
    position: absolute;
    left: 0;
    bottom: 0;
    width: 100%;
    background: linear-gradient(180deg, var(--brand-black) 0%, var(--brand-black) 30%, var(--brand-blue) 30%, var(--brand-blue) 100%);
  }
  .letterhead .footer-band { height: 36px; }
  .envelope .footer-band { height: 30px; }
  .flap { position: absolute; left: 0; top: 0; width: 100%; height: 90px; }
</style>
</head>
<body>

  <section class="sheet letterhead">
    <div class="brand-mark">
      <span class="brand-square"></span>
      <span>HARBORLINE<br>PROPERTY MANAGEMENT</span>
    </div>

    <div class="contact-block">
      <div class="contact-row">
        <svg viewBox="0 0 10 10"><rect x="0.5" y="2" width="9" height="7" rx="1.5" fill="#1457a8"/><rect x="2.5" y="0.5" width="5" height="2.5" rx="1" fill="#1457a8"/></svg>
        <span>+1 234 567 8901</span>
      </div>
      <div class="contact-row">
        <svg viewBox="0 0 10 10"><rect x="0.5" y="1" width="9" height="8" rx="1" fill="#1457a8"/><rect x="2" y="2.5" width="6" height="2" fill="#fff"/></svg>
        <span>+1 234 567 8901</span>
      </div>
      <div class="contact-row">
        <svg viewBox="0 0 10 10"><rect x="0.5" y="1.5" width="9" height="7" fill="#1457a8"/><path d="M1 2l4 3.5L9 2" stroke="#fff" fill="none" stroke-width="1"/></svg>
        <span>emailaddress@email.com</span>
      </div>
      <div class="contact-address">Address Line 1, Area<br>City Name, Area Name</div>
    </div>

    <div class="recipient">
      To<br>Lorem Ipsum is simply<br>Lorem Ipsum is Lorem Ipsum is<br>Lorem Ipsum is
    </div>

    <div class="letter-body">
      <p>&nbsp;dummy text of the printing and typesetting industry. Lorem Ipsum has been the industry's standard dummy text ever since the 1500s, when an unknown printer took a galley of type and scrambled it to make a type specimen book. It has survived not only five centuries, but also the leap into electronic typesetting, remaining essentially unchanged.</p>
      <p>It is a long established fact that a reader will be distracted by the readable content of a page when looking at its layout. The point of using Lorem Ipsum is that it has a more-or-less normal distribution of letters, as opposed to using 'Content here, content here', making it look like readable English. Many desktop publishing packages and web page editors now use Lorem Ipsum as their default</p>
      <p>&nbsp;Contrary to popular belief, Lorem Ipsum is not simply random text. It has roots in a piece of classical Latin literature from 45 BC, making it over 2000 years old. Tomas Venwick, a Latin professor at Alder Crest College in Oregon, looked up one of the more obscure Latin words, consectetur, from a Lorem Ipsum passage,</p>
    </div>

    <div class="sign-off">Lorem Ipsum</div>
    <div class="signature-area" role="img" aria-label="Handwritten signature"></div>
    <div class="signer-title">Lorem Ipsum is a dummy</div>

    <div class="footer-band" role="img" aria-label="Decorative curved footer swoosh in black and blue"></div>
  </section>

  <section class="sheet envelope envelope-front-band">
    <div class="brand-mark">
      <span class="brand-square"></span>
      <span>HARBORLINE<br>PROPERTY MGMT</span>
    </div>
    <div class="envelope-address">Address Line 1, Area,<br>City Name, Area<br>Name 8976</div>
    <div class="footer-band" role="img" aria-label="Decorative curved footer swoosh in black and blue"></div>
  </section>

  <section class="sheet envelope envelope-back-blue">
    <svg class="flap" viewBox="0 0 511 90" preserveAspectRatio="none" aria-hidden="true">
      <defs>
        <filter id="flap-shadow-blue" x="-5%" y="-20%" width="110%" height="150%">
          <feDropShadow dx="0" dy="3" stdDeviation="3" flood-color="#000" flood-opacity="0.35"/>
        </filter>
      </defs>
      <path d="M0 0 L511 0 L493 64 Q489 74 478 74 L33 74 Q22 74 18 64 Z" fill="var(--brand-blue)" filter="url(#flap-shadow-blue)"/>
    </svg>
  </section>

  <section class="sheet envelope envelope-front-plain">
    <div class="brand-mark">
      <span class="brand-square"></span>
      <span>HARBORLINE<br>PROPERTY MGMT</span>
    </div>
    <div class="envelope-address">Address Line 1, Area,<br>City Name, Area<br>Name 8976</div>
  </section>

  <section class="sheet envelope envelope-back-plain">
    <svg class="flap" viewBox="0 0 511 90" preserveAspectRatio="none" aria-hidden="true">
      <defs>
        <filter id="flap-shadow-white" x="-5%" y="-20%" width="110%" height="150%">
          <feDropShadow dx="0" dy="3" stdDeviation="3" flood-color="#000" flood-opacity="0.3"/>
        </filter>
      </defs>
      <path d="M0 0 L511 0 L493 64 Q489 74 478 74 L33 74 Q22 74 18 64 Z" fill="var(--paper)" filter="url(#flap-shadow-white)"/>
    </svg>
  </section>

</body>
</html>
```